Blog Banner Design Project: Wanderly Ledger

Looking for a new banner for my blog " Neville Ostrander's Wanderly Ledger" at http://www.wanderlyledger.net - and once design agreed also want an updated album art for the podcast that goes along with the site.
For more about the blog and what it is about:
http://www.wanderlyledger.net/about
Wanderly Ledger is a Luxury Travel Blog And Podcast that provides inspiration, advice and tips about luxurious travel experiences, including destinations, transportation, accommodation, and journeys, that travellers can read, listen to or watch.
Objective of the new design
(1) retain the colour scheme ideally to retain the brand identity, as have been using these colours since 2005.
(2) introduce more of my personality and make it more visually and overt that it is "Neville Ostrander's Wanderly Ledger", so possibly introducing my image into the blog banner so visitors are clear and more aware of the person behind the brand.
(3) needs to have an up-market, luxury but modern feel.
(4) if possible reflect the focus on the content (destinations, transportation, accommodation, attractions and journeys) - but this maybe best left to just words as want the design to be bold and more of the branding and personality.
Ideal wording
Smallish: Neville Ostrander's
Main wording: Wanderly Ledger
Sub-title/ small: luxurious destinations, transportation, accommodation and journeys.
I have a poll running with readers of my blog to rate the designs to help me to chose the final route, and so there is no need to submit any more designs. I will make the decision once the poll closes on the weekend.

```html
<!DOCTYPE html>
<html lang="en">
<head>
<meta charset="utf-8">
<title>Neville Ostrander's Wanderly Ledger – Blog Banner</title>
<link rel="stylesheet" href="https://fonts.googleapis.com/css2?family=Courgette&family=Lustria&family=Noticia+Text:wght@700&display=swap">
<style>
  :root {
    --photo-violet: #4b2f7d;
    --photo-lilac: #7a62a8;
    --photo-dusk: #8c5a8a;
    --photo-amber: #d48a2c;
    --photo-gold: #e7a63a;
    --tab-magenta: #c02a9c;
    --band-black: rgba(8, 6, 10, 0.88);
    --text-white: #ffffff;
    --text-blush: #fbe6f4;
  }

  html, body {
    margin: 0;
    padding: 0;
    overflow: hidden;
    background: #ffffff;
  }

  .banner {
    position: relative;
    width: 1200px;
    height: 202px;
    overflow: hidden;
  }

  .banner__collage {
    position: absolute;
    inset: 0;
    background:
      radial-gradient(ellipse 180px 150px at 95px 110px, rgba(150, 130, 170, 0.55), transparent 70%),
      linear-gradient(180deg, rgba(255,255,255,0.06), rgba(0,0,0,0.12)),
      linear-gradient(90deg,
        var(--photo-lilac) 0%,
        var(--photo-violet) 22%,
        #5d4390 42%,
        var(--photo-dusk) 62%,
        var(--photo-amber) 82%,
        var(--photo-gold) 100%);
  }

  .banner__shapes {
    position: absolute;
    inset: 0;
  }

  .byline {
    position: absolute;
    left: 300px;
    top: 13px;
    margin: 0;
    font-family: "Courgette", cursive;
    font-weight: 400;
    font-size: 29px;
    line-height: 38px;
    color: var(--text-blush);
    white-space: nowrap;
  }

  .masthead {
    position: absolute;
    left: 300px;
    top: 56px;
    margin: 0;
    font-family: "Lustria", serif;
    font-weight: 400;
    font-size: 54px;
    line-height: 66px;
    letter-spacing: 0.5px;
    color: var(--text-white);
    white-space: nowrap;
  }

  .tagline {
    position: absolute;
    left: 434px;
    top: 164px;
    margin: 0;
    font-family: "Noticia Text", serif;
    font-weight: 700;
    font-size: 18px;
    line-height: 34px;
    color: var(--text-white);
    white-space: nowrap;
  }
</style>
</head>
<body>
  <header class="banner">
    <div class="banner__collage" role="img"
         aria-label="Travel photo collage in violet to amber tones: beach, waterfall, city skyline, Eiffel Tower and an old map, with a portrait of Neville Ostrander at the left"></div>

    <svg class="banner__shapes" width="1200" height="202" viewBox="0 0 1200 202" aria-hidden="true">
      <polygon class="byline-tab" points="292,12 566,12 556,52 280,52" fill="var(--tab-magenta)"/>
      <polygon class="masthead-band" points="268,55 990,55 970,122 252,122" fill="var(--band-black)"/>
      <polygon class="tagline-band" points="430,163 1200,163 1200,198 417,198" fill="var(--band-black)"/>
    </svg>

    <p class="byline">Neville Ostrander's</p>
    <h1 class="masthead">Wanderly Ledger</h1>
    <p class="tagline">Luxurious destinations, transportation, accommodation and journeys.</p>
  </header>
</body>
</html>
```